Health Clinic treating people with mental illness needs a website

We need a website for a new mental health clinic based in Florida called Solvane Wellness USA. We treat people with mental health issues such as depression, PTSD, Bipolar, chronic pain, etc. I want the website to be easy to follow and inviting to the visitors. It should be easy to locate the different treatment options and how to go about contacting and making appointments. The images on the website should be something that the patients can relate to, whether a close up of a woman's face, something that conveys emotion. The patients visiting this website are often sad and miserable, they need to be able to feel comfortable when they look at this website. I want them to feel that we understand where they are coming from. I like colors such as purple, turquoise, lavender.

Target Market(s)

College students, veterans, anyone with mental illness

Industry/Entity Type

Health And Wellness

Font styles to use
Serif
Sans Serif

Colors

Designer to choose colors to be used in the design.

Requirements
Must have
• There should be a home/landing page, about us page, treatment page, contact page, and a FAQ page. I've included my logo below.
Nice to have
• The flow of the web pages should be calming and welcoming. I want people to feel warm and understood when they enter our page.
Should not have
• The images and writing should not be overly stimulating or aggressive.

```html
<!DOCTYPE html>
<html lang="en">
<head>
<meta charset="utf-8">
<title>Solvane Wellness USA</title>
<link href="https://fonts.googleapis.com/css2?family=Poppins:ital,wght@0,300;0,400;0,500;0,600;0,700;1,300;1,400&family=Lato:wght@400&display=swap" rel="stylesheet">
<style>
:root{
  --teal:#2eab91;
  --teal-soft:#78c7b9;
  --purple:#a6529d;
  --plum:#4b1a6b;
  --lavender:#f3e6f0;
  --ink:#111;
  --body:#222;
  --pink-strip:#c98fc4;
  --white:#fff;
}
*{margin:0;padding:0;box-sizing:border-box}
html,body{width:1200px;height:2786px;overflow:hidden;background:var(--white)}
body{position:relative;font-family:"Lato",sans-serif;color:var(--body)}
.abs{position:absolute}
.brand{left:108px;top:52px;font-family:"Poppins",sans-serif;font-weight:600;font-size:28px;color:var(--plum);display:flex;align-items:center;gap:10px;line-height:1}
.brand-dot{width:14px;height:14px;border-radius:50%;background:var(--plum)}
.book-btn{left:862px;top:22px;width:226px;height:52px;background:var(--teal);color:var(--white);font-family:"Poppins",sans-serif;font-size:16px;display:flex;align-items:center;justify-content:center}
.nav{top:97px;font-family:"Poppins",sans-serif;font-size:15px;font-weight:500;color:var(--ink);letter-spacing:.2px}
.nav.active{color:var(--teal)}
.header-rule{left:0;top:134px;width:1200px;height:1px;background:#e6e6e6}
.hero-panel{left:0;top:135px;width:597px;height:470px;background:var(--teal)}
.hero-title{left:0;width:597px;top:306px;text-align:center;color:var(--white);font-family:"Poppins",sans-serif}
.hero-title .strong{display:block;font-weight:700;font-size:52px;line-height:64px}
.hero-title .light{display:block;font-weight:300;font-size:47px;line-height:60px}
.hero-photo{left:597px;top:135px;width:603px;height:470px;background:linear-gradient(135deg,#6f9a9a 0%,#b9a393 45%,#8fb7b6 100%)}
.about-band{left:0;top:683px;width:1200px;height:470px;background:var(--lavender)}
.section-title{left:0;width:1200px;text-align:center;font-family:"Poppins",sans-serif;font-weight:700;font-size:39px;color:var(--ink)}
.about-copy{left:235px;width:730px;top:834px;text-align:center;font-size:17px;line-height:30px;color:var(--body)}
.about-photo{left:238px;top:966px;width:724px;height:447px;background:linear-gradient(90deg,#9a9a8f 0%,#6c6a63 40%,#7e7875 70%,#5e5c5a 100%)}
.t-card{top:1634px;width:326px;height:313px;color:var(--white);text-align:center;padding:0 32px}
.t-card h3{font-family:"Poppins",sans-serif;font-weight:600;font-size:26px;line-height:30px;margin-top:54px}
.t-card p{font-size:17px;line-height:25.7px;margin-top:20px}
.t-ptsd{left:111px;background:linear-gradient(160deg,#b9909f 0%,#8b6b8e 45%,#6f5a7c 100%);height:300px}
.t-ptsd-strip{left:111px;top:1934px;width:326px;height:13px;background:var(--pink-strip)}
.t-bipolar{left:437px;background:var(--teal-soft)}
.t-pain{left:763px;background:var(--purple)}
.articles-band{left:0;top:2025px;width:1200px;height:683px;background:var(--lavender)}
.articles-title{left:0;width:1200px;top:2100px;text-align:center;font-family:"Poppins",sans-serif;font-style:italic;font-weight:300;font-size:39px;color:var(--ink);letter-spacing:.5px}
.articles-panel{left:111px;top:2188px;width:977px;height:457px;background:var(--white)}
.a-card{top:2221px;width:292px;height:312px;background:var(--white);box-shadow:0 1px 6px rgba(0,0,0,.12)}
.a-img{height:167px}
.a-title{position:absolute;left:25px;top:192px;font-family:"Poppins",sans-serif;font-style:italic;font-size:17px;color:#222}
.a-rule{position:absolute;left:24px;top:253px;width:243px;height:2px;background:#999}
.a-meta{position:absolute;left:24px;top:270px;width:243px;display:flex;align-items:center;font-family:"Poppins",sans-serif;font-size:12px;color:#333}
.a-meta .count{font-size:14px;margin:0 14px 0 8px}
.a-meta .heart{margin-left:auto}
.more-btn{left:126px;top:2573px;width:159px;height:42px;background:var(--teal-soft);color:var(--white);font-size:15px;display:flex;align-items:center;justify-content:center}
.social{top:2736px;width:20px;height:20px;border-radius:50%;background:var(--ink)}
.copyright{right:115px;top:2736px;font-size:16px;color:var(--ink)}
</style>
</head>
<body>

<header>
  <div class="abs brand"><span class="brand-dot"></span>Solvane Wellness USA</div>
  <a class="abs book-btn">Book an Appointment</a>
  <span class="abs nav active" style="left:564px">HOME</span>
  <span class="abs nav" style="left:653px">ABOUT US</span>
  <span class="abs nav" style="left:775px">TREATMENT</span>
  <span class="abs nav" style="left:910px">FAQ</span>
  <span class="abs nav" style="left:985px">CONTACT US</span>
  <div class="abs header-rule"></div>
</header>

<section class="hero">
  <div class="abs hero-panel"></div>
  <h1 class="abs hero-title"><span class="strong">SOLVANE</span><span class="light">WELLNESS USA</span></h1>
  <div class="abs hero-photo" role="img" aria-label="Close-up photo of a distressed woman holding her temples"></div>
</section>

<section class="about">
  <div class="abs about-band"></div>
  <h2 class="abs section-title" style="top:748px">ABOUT</h2>
  <p class="abs about-copy">Lorem ipsum dolor sit amet, consectetur adipiscing elit, sed do eiusmod tempor incididunt ut labore et dolore magna aliqua. Quis ipsum suspendisse ultrices gravida. Risus commodo viverra maecenas accumsan lacus vel facilisis. Lorem ipsum dolor sit amet,</p>
  <div class="abs about-photo" role="img" aria-label="Photo of a therapist taking notes while a patient sits opposite"></div>
</section>

<section class="treatment">
  <h2 class="abs section-title" style="top:1537px">TREATMENT</h2>
  <div class="abs t-card t-ptsd" role="img" aria-label="PTSD treatment card over a photo of a comforting hand on a shoulder">
    <h3>PTSD<br>TREATMENT</h3>
    <p>Lorem ipsum dolor sit amet, con-sectetur adipiscing elit, sed do eius-mod tempor incididunt ut labore et dolore magna aliqua.</p>
  </div>
  <div class="abs t-ptsd-strip"></div>
  <div class="abs t-card t-bipolar">
    <h3>BIPOLAR<br>TREATMENT</h3>
    <p>Lorem ipsum dolor sit amet, con-sectetur adipiscing elit, sed do eius-mod tempor incididunt ut labore et dolore magna aliqua.</p>
  </div>
  <div class="abs t-card t-pain">
    <h3>CHRONIC PAIN<br>TREATMENT</h3>
    <p>Lorem ipsum dolor sit amet, con-sectetur adipiscing elit, sed do eius-mod tempor incididunt ut labore et dolore magna aliqua.</p>
  </div>
</section>

<section class="articles">
  <div class="abs articles-band"></div>
  <h2 class="abs articles-title">ARTICLES&nbsp; ABOUT PSYCHOLOGY</h2>
  <div class="abs articles-panel"></div>

  <article class="abs a-card" style="left:126px">
    <div class="a-img" role="img" aria-label="Photo of a woman with a headache" style="background:linear-gradient(135deg,#d9d4d0,#a88a7c 55%,#e6e2de)"></div>
    <span class="a-title">Understanding PTSD</span>
    <div class="a-rule"></div>
    <div class="a-meta">
      <svg width="18" height="12" viewBox="0 0 18 12"><path d="M1 6C4 1 14 1 17 6C14 11 4 11 1 6Z" fill="#333"/><circle cx="9" cy="6" r="2.4" fill="#fff"/></svg>
      <span class="count">0</span><span>Write a Comment</span>
      <svg class="heart" width="12" height="11" viewBox="0 0 12 11"><path d="M6 10L1.5 5.5A2.6 2.6 0 0 1 6 2A2.6 2.6 0 0 1 10.5 5.5Z" fill="none" stroke="#e0344b" stroke-width="1.3"/></svg>
    </div>
  </article>

  <article class="abs a-card" style="left:452px">
    <div class="a-img" role="img" aria-label="Photo of a woman covering her face with a double-exposure effect" style="background:linear-gradient(135deg,#1a1a1a,#6a5d58 50%,#141414)"></div>
    <span class="a-title">Understanding Bipolar</span>
    <div class="a-rule"></div>
    <div class="a-meta">
      <svg width="18" height="12" viewBox="0 0 18 12"><path d="M1 6C4 1 14 1 17 6C14 11 4 11 1 6Z" fill="#333"/><circle cx="9" cy="6" r="2.4" fill="#fff"/></svg>
      <span class="count">0</span><span>Write a Comment</span>
      <svg class="heart" width="12" height="11" viewBox="0 0 12 11"><path d="M6 10L1.5 5.5A2.6 2.6 0 0 1 6 2A2.6 2.6 0 0 1 10.5 5.5Z" fill="none" stroke="#e0344b" stroke-width="1.3"/></svg>
    </div>
  </article>

  <article class="abs a-card" style="left:777px">
    <div class="a-img" role="img" aria-label="Photo of a woman holding her neck in pain" style="background:linear-gradient(135deg,#c9ced3,#b08e7e 50%,#eef0f1)"></div>
    <span class="a-title">Understanding Chronic</span>
    <div class="a-rule"></div>
    <div class="a-meta">
      <svg width="18" height="12" viewBox="0 0 18 12"><path d="M1 6C4 1 14 1 17 6C14 11 4 11 1 6Z" fill="#333"/><circle cx="9" cy="6" r="2.4" fill="#fff"/></svg>
      <span class="count">0</span><span>Write a Comment</span>
      <svg class="heart" width="12" height="11" viewBox="0 0 12 11"><path d="M6 10L1.5 5.5A2.6 2.6 0 0 1 6 2A2.6 2.6 0 0 1 10.5 5.5Z" fill="none" stroke="#e0344b" stroke-width="1.3"/></svg>
    </div>
  </article>

  <a class="abs more-btn">MORE ARTICLES</a>
</section>

<footer>
  <span class="abs social" style="left:112px" aria-label="Social link"></span>
  <span class="abs social" style="left:146px" aria-label="Social link"></span>
  <span class="abs copyright">© 2019 BY SOLVANE WELLNESS</span>
</footer>

</body>
</html>
```